Biz Card

MARKETING today is the most rapidly changing business discipline. Media options to reach customers, actual customer preferences and consumer buying decisions change by the minute . . . no, by the second. The behavioral data generated by all aspects of the business and the new technologies that put the data to work together produce the potential to generate business intelligence and guide smart resource allocation to influence purchase and retention. However, to realize this potential, marketing professionals at all levels and in all organizations must continuously improve their skills not just from on-the-job training but by learning from masters in the field. The Bright Horizon Guild is the training center that serves this professional development need.model logos:msi.orgama.orgcontentmarketinginstitute.comBook covers on MarketingMetrics, Marketing Anaytics
Industry/Entity Type
Business
Contact Information for Business Card
Roy A. YoungCEOMarketing Science Academyphone: 310-601-4755email: roy@marketingscience.comAddress:437 South Rexford DriveBeverly Hills, CA 89377
Look and feel
Each slider illustrates characteristics of the customer's brand and the style your logo design should communicate.

```html
<!DOCTYPE html>
<html lang="en">
<head>
<meta charset="utf-8">
<title>Bright Horizon Guild – Business Card</title>
<link rel="stylesheet" href="https://fonts.googleapis.com/css2?family=Roboto:wght@400;500;700&display=swap">
<style>
  :root {
    --backdrop: #c9c7c7;
    --paper: #fbfbfb;
    --brand-red: #8d2624;
    --brand-grey: #555152;
    --ink: #4a4a4a;
    --white: #ffffff;
  }
  * { margin: 0; padding: 0; box-sizing: border-box; }
  html, body { width: 1200px; height: 1200px; overflow: hidden; }
  body {
    background: var(--backdrop);
    font-family: "Roboto", Arial, sans-serif;
    position: relative;
  }
  .card {
    position: absolute;
    width: 714px;
    height: 418px;
    background: var(--paper);
    overflow: hidden;
  }
  .card--front { left: 238px; top: 119px; }
  .card--back  { left: 230px; top: 643px; }

  .card__band {
    position: absolute;
    left: 0; right: 0; bottom: 0;
    height: 16px;
    background: var(--brand-red);
  }

  .wordmark {
    position: absolute;
    display: flex;
    align-items: center;
    gap: 14px;
    color: var(--brand-red);
    font-weight: 700;
    font-size: 44px;
    letter-spacing: -0.5px;
    white-space: nowrap;
  }
  .wordmark__dot {
    width: 18px; height: 18px;
    border-radius: 50%;
    background: var(--brand-red);
  }
  .card--front .wordmark { left: 0; right: 0; top: 178px; justify-content: center; }
  .card--back .wordmark { left: 40px; top: 136px; }

  .card__wave { position: absolute; left: 0; top: 0; }

  .holder {
    position: absolute;
    right: 46px;
    top: 36px;
    text-align: right;
    color: var(--white);
  }
  .holder__name { font-size: 25px; font-weight: 500; }
  .holder__title { font-size: 15px; margin-top: 8px; letter-spacing: 0.5px; }

  .contact {
    position: absolute;
    left: 40px;
    top: 282px;
    list-style: none;
    color: var(--ink);
    font-size: 18px;
  }
  .contact__item { display: flex; align-items: center; height: 24px; }
  .contact__icon { width: 16px; height: 16px; margin-right: 20px; fill: var(--brand-red); }
  .address {
    position: absolute;
    left: 40px;
    top: 361px;
    color: var(--ink);
    font-size: 18px;
  }
</style>
</head>
<body>

<section class="card card--front">
  <div class="wordmark"><span class="wordmark__dot"></span>Bright Horizon Guild</div>
  <div class="card__band"></div>
</section>

<section class="card card--back">
  <svg class="card__wave" width="714" height="418" viewBox="0 0 714 418">
    <path fill="var(--brand-red)" d="M0 0 H714 V175 C600 170 500 130 420 80 C330 25 200 -5 0 45 Z"/>
    <path fill="var(--brand-grey)" d="M0 48 C150 8 300 10 400 70 C300 30 150 35 0 80 Z"/>
  </svg>

  <div class="holder">
    <div class="holder__name">Neil P. Barton</div>
    <div class="holder__title">CEO</div>
  </div>

  <div class="wordmark"><span class="wordmark__dot"></span>Bright Horizon Guild</div>

  <ul class="contact">
    <li class="contact__item">
      <svg class="contact__icon" viewBox="0 0 16 16"><path d="M2 5 C2 2 14 2 14 5 L14 7 L11 7 L11 5.5 L5 5.5 L5 7 L2 7 Z M4 8 H12 L13.5 14 H2.5 Z"/></svg>
      310-555-0182
    </li>
    <li class="contact__item">
      <svg class="contact__icon" viewBox="0 0 16 16"><path d="M1 3 H15 V13 H1 Z M2 4 L8 9 L14 4 Z" fill-rule="evenodd"/></svg>
      neil@brighthorizonguild.com
    </li>
    <li class="contact__item">
      <svg class="contact__icon" viewBox="0 0 16 16"><circle cx="8" cy="8" r="6.5" fill="none" stroke="var(--brand-red)" stroke-width="1.4"/><ellipse cx="8" cy="8" rx="2.8" ry="6.5" fill="none" stroke="var(--brand-red)" stroke-width="1.2"/><path d="M1.5 8 H14.5" stroke="var(--brand-red)" stroke-width="1.2"/></svg>
      www.brighthorizonguild.com
    </li>
  </ul>
  <p class="address">912 North Calloway Lane Beverly Hills, CA 89377</p>
</section>

</body>
</html>
```